Business Cards for a law firm

Business cards for our law firm. Use our silhoette logo and OAK PARTNERS - check our website (www.oakpartners.example)

Contact Information for Business Card

our silhouette logo, OAK PARTNERS, 800-555-0147, Dorian Pemberton, dorian@oakpartners.example

Requirements
Must have
• our silhouette logo, OAK PARTNERS, 800-555-0147, Dorian Pemberton, dorian@oakpartners.example

```html
<!DOCTYPE html>
<html lang="en">
<head>
<meta charset="utf-8">
<title>Oak Partners – Business Cards</title>
<link rel="stylesheet" href="https://fonts.googleapis.com/css2?family=Cinzel:wght@600&family=Arimo:wght@400&display=swap">
<style>
  :root {
    --backdrop: #9b9b9b;
    --paper: #f7f7f5;
    --navy: #1a2e68;
    --navy-deep: #172b63;
    --ink: #2b2b2b;
    --rule: #9a9a9a;
  }
  * { box-sizing: border-box; margin: 0; padding: 0; }
  html, body {
    width: 1200px; height: 1050px; overflow: hidden;
    background: var(--backdrop);
  }
  .canvas { position: relative; width: 1200px; height: 1050px; }
  .card {
    position: absolute;
    width: 700px; height: 400px;
    border-radius: 26px;
    box-shadow: 0 6px 18px rgba(0,0,0,0.22);
  }
  .card--front { left: 140px; top: 90px; background: var(--paper); }
  .card--back { left: 360px; top: 560px; background: var(--navy-deep); }

  .brand {
    position: absolute;
    display: flex; align-items: center; gap: 22px;
    font-family: "Cinzel", serif; font-weight: 600;
    letter-spacing: 0.08em;
  }
  .brand__mark { width: 58px; height: 58px; }
  .brand__name { font-size: 46px; line-height: 1; white-space: nowrap; }

  .card--front .brand { left: 90px; top: 110px; color: var(--navy); }
  .card--front .brand__mark { background: var(--navy); }
  .card--back .brand { left: 120px; top: 168px; color: #ffffff; }
  .card--back .brand__mark { background: #ffffff; }

  .holder {
    position: absolute; left: 70px; top: 262px;
    font-family: "Cinzel", serif; font-weight: 600;
    font-size: 25px; letter-spacing: 0.04em;
    color: var(--navy); white-space: nowrap;
  }
  .divider {
    position: absolute; left: 380px; top: 250px;
    width: 1px; height: 92px; background: var(--rule);
  }
  .contact {
    position: absolute; left: 404px; top: 252px;
    list-style: none;
    font-family: "Arimo", sans-serif; font-size: 19px;
    color: var(--ink);
  }
  .contact li { display: flex; align-items: center; gap: 10px; height: 29px; white-space: nowrap; }
  .contact svg { width: 16px; height: 16px; flex: none; fill: var(--navy); }
</style>
</head>
<body>
<main class="canvas">
  <section class="card card--front" aria-label="Business card front">
    <div class="brand">
      <span class="brand__mark"></span>
      <span class="brand__name">OAK PARTNERS</span>
    </div>
    <p class="holder">Dorian Pemberton</p>
    <span class="divider"></span>
    <ul class="contact">
      <li>
        <svg viewBox="0 0 16 16" aria-hidden="true"><path d="M3.5 1.5l2.3 0 1 3.2-1.6 1.2c.8 1.8 2.2 3.2 4 4l1.2-1.6 3.2 1v2.3c0 .8-.7 1.4-1.5 1.4C6.6 13 3 9.4 2.1 3c0-.8.6-1.5 1.4-1.5z"/></svg>
        800-555-0147
      </li>
      <li>
        <svg viewBox="0 0 16 16" aria-hidden="true"><path d="M1 3.5h14v9H1z M1.6 4l6.4 5 6.4-5" fill="none" stroke="#1a2e68" stroke-width="1.4"/></svg>
        dorian@oakpartners.example
      </li>
      <li>
        <svg viewBox="0 0 16 16" aria-hidden="true"><circle cx="8" cy="8" r="7"/><path d="M1 8h14M8 1c2.4 2.2 2.4 11.8 0 14M8 1c-2.4 2.2-2.4 11.8 0 14" fill="none" stroke="#f7f7f5" stroke-width="1"/></svg>
        www.oakpartners.example
      </li>
    </ul>
  </section>

  <section class="card card--back" aria-label="Business card back">
    <div class="brand">
      <span class="brand__mark"></span>
      <span class="brand__name">OAK PARTNERS</span>
    </div>
  </section>
</main>
</body>
</html>
```